velmora - business cards

Need business card designs - logo provided - see www.velmora.co.nz

Industry/Entity Type

Business

Requirements
Must have
• logo - provided in attachments
• www.velmora.co.nz

```html
<!DOCTYPE html>
<html lang="en">
<head>
<meta charset="utf-8">
<title>velmora – business cards</title>
<link rel="stylesheet" href="https://fonts.googleapis.com/css2?family=Ubuntu:wght@400;500;700&display=swap">
<style>
  :root {
    --backdrop: #2a2a2a;
    --orange: #ef7426;
    --orange-deep: #a9501b;
    --orange-light: #f48434;
    --charcoal: #3b3b3d;
    --charcoal-band: #4a4a4c;
    --paper: #fbfbfb;
    --paper-shade: #ececec;
    --url-grey: #d9d6d3;
  }
  * { box-sizing: border-box; margin: 0; padding: 0; }
  html, body {
    width: 1200px;
    height: 814px;
    overflow: hidden;
    background: var(--backdrop);
    font-family: "Ubuntu", sans-serif;
  }
  .stage {
    position: relative;
    width: 1200px;
    height: 814px;
    display: flex;
    justify-content: center;
    align-items: center;
    gap: 120px;
  }
  .card {
    position: relative;
    width: 340px;
    height: 600px;
    overflow: hidden;
  }

  /* Front */
  .card-front {
    background: linear-gradient(180deg, var(--orange-deep) 0%, var(--orange) 45%, var(--orange-light) 55%, var(--orange-deep) 100%);
  }
  .front-wordmark {
    position: absolute;
    top: 140px;
    left: 0;
    right: 0;
    text-align: center;
    font-size: 62px;
    font-weight: 500;
    color: var(--charcoal);
    letter-spacing: 0.5px;
  }
  .front-url {
    position: absolute;
    bottom: 44px;
    left: 0;
    right: 0;
    text-align: center;
    font-size: 22px;
    font-weight: 700;
    color: var(--url-grey);
  }

  /* Back */
  .card-back {
    background: linear-gradient(180deg, var(--paper) 0%, var(--paper-shade) 100%);
    padding: 0 34px;
  }
  .back-wordmark {
    margin-top: 78px;
    text-align: center;
    font-size: 40px;
    font-weight: 500;
    color: var(--orange);
  }
  .holder {
    margin-top: 42px;
    text-align: center;
  }
  .holder-name {
    font-size: 29px;
    font-weight: 700;
    color: var(--charcoal);
    line-height: 1.05;
  }
  .holder-role {
    font-size: 20px;
    font-weight: 700;
    color: var(--orange);
  }
  .holder-address {
    margin-top: 30px;
    text-align: center;
    font-size: 18px;
    font-weight: 700;
    color: var(--charcoal);
  }
  .contact-list {
    list-style: none;
    margin-top: 62px;
    font-size: 17px;
    font-weight: 700;
    color: var(--charcoal);
    line-height: 1.45;
  }
  .contact-label { color: var(--orange); margin-right: 4px; }
  .back-swoosh {
    position: absolute;
    left: 0;
    bottom: 0;
    width: 340px;
    height: 150px;
    display: block;
  }
</style>
</head>
<body>
  <main class="stage">
    <section class="card card-front" aria-label="Business card front">
      <div class="front-wordmark">velmora</div>
      <div class="front-url">www.velmora.co.nz</div>
    </section>

    <section class="card card-back" aria-label="Business card back">
      <div class="back-wordmark">velmora</div>
      <div class="holder">
        <div class="holder-name">YOUR NAME</div>
        <div class="holder-role">Company Position</div>
      </div>
      <div class="holder-address">Your Address</div>
      <ul class="contact-list">
        <li><span class="contact-label">P:</span>000 123 4567</li>
        <li><span class="contact-label">E:</span>youremail@domain.com</li>
      </ul>
      <svg class="back-swoosh" viewBox="0 0 340 150" preserveAspectRatio="none" aria-hidden="true">
        <path d="M0 18 C110 30 230 62 340 108 L340 150 L0 150 Z" fill="var(--orange)"/>
        <path d="M0 34 C110 46 230 78 340 122 L340 150 L0 150 Z" fill="var(--charcoal-band)"/>
      </svg>
    </section>
  </main>
</body>
</html>
```